Velmora Freightway Solutions Business cards

Would like a very unique design catchy but professional for business cards. Please use log provided.Marlon WellsCeo and Founder TransCon Logistix Solutions1-888-913-3225mwells@tlsolutionsus.comwww.tlsolutionsus.com

```html
<!DOCTYPE html>
<html lang="en">
<head>
<meta charset="utf-8">
<title>Velmora Freightway Solutions – Business Cards</title>
<link rel="stylesheet" href="https://fonts.googleapis.com/css2?family=Josefin+Sans:wght@700&family=Lato:wght@400;700&display=swap">
<style>
  :root {
    --stage: #5a5a5a;
    --card-white: #ffffff;
    --brand-blue: #1173bb;
    --brand-red: #ec1c24;
    --ink-light: #ffffff;
  }
  * { margin: 0; padding: 0; box-sizing: border-box; }
  html, body { width: 1200px; height: 802px; overflow: hidden; }
  body {
    background: var(--stage);
    position: relative;
    font-family: "Lato", Arial, sans-serif;
  }
  .card {
    position: absolute;
    top: 274px;
    width: 442px;
    height: 265px;
    background: var(--card-white);
    overflow: hidden;
    box-shadow: 0 3px 6px rgba(0,0,0,0.35);
  }
  .card--front { left: 136px; }
  .card--back { left: 624px; }

  .front-panel {
    position: absolute;
    left: 0; top: 0;
    width: 271px; height: 100%;
    background: var(--brand-blue);
  }
  .front-accent {
    position: absolute;
    left: 314px; top: 49px;
    width: 128px; height: 207px;
    background: var(--brand-red);
  }
  .contact-block {
    position: absolute;
    left: 24px; top: 134px;
    color: var(--ink-light);
  }
  .person-name {
    font-family: "Josefin Sans", Arial, sans-serif;
    font-weight: 700;
    font-size: 17px;
    letter-spacing: 0.3px;
    line-height: 1;
  }
  .person-title {
    font-size: 13px;
    margin-top: 2px;
  }
  .contact-list {
    list-style: none;
    margin-top: 26px;
    font-size: 12.5px;
    line-height: 16px;
  }
  .contact-list li { display: flex; align-items: center; gap: 5px; }
  .contact-list svg { width: 10px; height: 10px; fill: var(--ink-light); flex: none; }

  .back-brand {
    position: absolute;
    left: 0; right: 0; top: 108px;
    display: flex; justify-content: center; align-items: center; gap: 8px;
  }
  .brand-square {
    width: 14px; height: 14px;
    background: var(--brand-red);
  }
  .brand-name {
    font-family: "Lato", Arial, sans-serif;
    font-weight: 700;
    font-size: 20px;
    color: var(--brand-blue);
    letter-spacing: 0.5px;
  }
  .back-rule {
    position: absolute;
    left: 100px; right: 100px; top: 142px;
    height: 2px;
    background: var(--brand-red);
  }
  .back-url {
    position: absolute;
    left: 0; right: 0; top: 216px;
    text-align: center;
    font-size: 9.5px;
    font-weight: 700;
    letter-spacing: 0.6px;
    color: var(--brand-blue);
    text-transform: uppercase;
  }
</style>
</head>
<body>
  <section class="card card--front">
    <div class="front-panel"></div>
    <div class="front-accent"></div>
    <div class="contact-block">
      <p class="person-name">DORIAN PIKE</p>
      <p class="person-title">CEO and Founder</p>
      <ul class="contact-list">
        <li><svg viewBox="0 0 10 10"><path d="M1 4 Q5 0 9 4 L7.5 5 L6.5 3.8 L3.5 3.8 L2.5 5 Z M2.5 5.5 H7.5 L8.5 9 H1.5 Z"/></svg>1-888-470-6158</li>
        <li><svg viewBox="0 0 10 10"><path d="M0.5 2 H9.5 V8 H0.5 Z M1.2 2.6 L5 5.6 L8.8 2.6" stroke="#1173bb" stroke-width="0.8"/></svg>dpike@vfwayroutes.com</li>
        <li><svg viewBox="0 0 10 10"><circle cx="5" cy="5" r="4.5"/><path d="M2 4 Q4 3 5 5 T8 6" stroke="#1173bb" stroke-width="0.8" fill="none"/></svg>www.vfwayroutes.com</li>
      </ul>
    </div>
  </section>

  <section class="card card--back">
    <div class="back-brand">
      <span class="brand-square"></span>
      <span class="brand-name">Velmora Freightway Solutions</span>
    </div>
    <div class="back-rule"></div>
    <p class="back-url">www.vfwayroutes.com</p>
  </section>
</body>
</html>
```